Clean business card with logo provided

I want a card that will stand out among the masses. I need the color and image to show professionalism and yet have a family appeal showing that I only deal with win/win scenarios. The back of the card will be used to take notes about the individual so I can use that in my database entry. I like modern design but need professionalism in it also. It needs to fit my "clean, safe, and affordable housing" motto. I need to be able to write on the file and update the card details for my employees.

Target Market(s)

Investors looking to make investment income through real estate

Industry/Entity Type

Real Estate

Contact Information for Business Card

Brent Kovalich
blank address, city, st, zip code
480-555-3174
brentkovalich@ridgeworthrentals.example
www.ridgeworthrentals.example

Font styles to use
Sans Serif

Requirements
Must have
• I would like the back of the card to have lines for info. example
• Met/Visited: Date:
• Interets:
Nice to have
• I want the cards color to match the logo background color. Font with details to be san serif and black. I want the card rectangular with square corners. Standard business card size. I would like to see cards designed with both images to see which i prefer more.

```html
<!DOCTYPE html>
<html lang="en">
<head>
<meta charset="utf-8">
<title>Ridgeworth Rentals LLC – Business Card</title>
<link rel="stylesheet" href="https://fonts.googleapis.com/css2?family=Marcellus&family=Montserrat:wght@400;600&display=swap">
<style>
  :root {
    --page-bg: #e9e6e1;
    --card-black: #0b0b0c;
    --brand-cyan: #2bbfd6;
    --paper-white: #ffffff;
    --ink-black: #111111;
    --rule-grey: #3a3a3a;
  }
  * { box-sizing: border-box; margin: 0; padding: 0; }
  html, body { width: 1200px; height: 950px; overflow: hidden; }
  body {
    background: var(--page-bg);
    position: relative;
    font-family: "Montserrat", sans-serif;
  }
  .card { position: absolute; overflow: hidden; box-shadow: 0 6px 18px rgba(0,0,0,.18); }

  /* Front */
  .card-front {
    left: 70px; top: 315px; width: 560px; height: 320px;
    background: var(--card-black);
    display: flex; flex-direction: column; align-items: center; justify-content: center;
  }
  .brand-name {
    font-family: "Marcellus", serif;
    color: var(--brand-cyan);
    font-size: 40px;
    letter-spacing: 3px;
    text-transform: uppercase;
    text-align: center;
    line-height: 1.1;
  }
  .brand-rule { width: 330px; height: 1px; background: var(--paper-white); margin: 10px 0 8px; }
  .brand-tagline { color: var(--brand-cyan); font-size: 12px; letter-spacing: .5px; }

  /* Back */
  .card-back {
    left: 720px; top: 160px; width: 360px; height: 630px;
    background: var(--brand-cyan);
  }
  .contact {
    position: absolute; left: 40px; top: 34px;
    color: var(--ink-black); font-size: 14px; line-height: 1.55;
  }
  .contact-name {
    font-family: "Marcellus", serif;
    font-size: 26px; letter-spacing: 2px; text-transform: uppercase;
    margin-bottom: 6px;
  }
  .back-art { position: absolute; left: 0; top: 0; width: 360px; height: 630px; }
  .notes {
    position: absolute; left: 26px; top: 390px; width: 230px;
    color: var(--brand-cyan); font-size: 14px; font-weight: 600; letter-spacing: .5px;
  }
  .note-line {
    display: flex; align-items: flex-end; gap: 6px;
    height: 36px; text-transform: uppercase;
  }
  .note-line .rule { flex: 1; border-bottom: 1px solid var(--rule-grey); margin-bottom: 4px; }
  .note-blank { height: 36px; border-bottom: 1px solid var(--rule-grey); }
</style>
</head>
<body>
  <section class="card card-front" aria-label="Card front">
    <div class="brand-name">Ridgeworth Rentals LLC</div>
    <div class="brand-rule"></div>
    <div class="brand-tagline">Providing clean, safe, and affordable housing</div>
  </section>

  <section class="card card-back" aria-label="Card back">
    <svg class="back-art" viewBox="0 0 360 630" aria-hidden="false">
      <rect x="120" y="250" width="240" height="200" fill="#0b0b0c" role="img" aria-label="Large dark brand illustration area"/>
      <path d="M0 340 C 90 320, 140 360, 200 420 S 300 540, 360 560 L 360 630 L 0 630 Z" fill="#ffffff"/>
    </svg>
    <div class="contact">
      <div class="contact-name">Brent Kovalich</div>
      <div>brentkovalich@ridgeworthrentals.example</div>
      <div>1420 Larkspur Court</div>
      <div>Anchorage, Alaska 34512</div>
      <div>P : 480-555-3174</div>
      <div>www.ridgeworthrentals.example</div>
    </div>
    <div class="notes">
      <div class="note-line">Met/Visited:<span class="rule"></span></div>
      <div class="note-line">Date:<span class="rule"></span></div>
      <div class="note-line">Interests:<span class="rule"></span></div>
      <div class="note-blank"></div>
      <div class="note-blank"></div>
    </div>
  </section>
</body>
</html>
```